New Bicycle shop business card

Hi!
I'm looking for a business card for my new proffesional bike mechanics shop. This shop is only for fixing broken bikes and not selling bikes.
Peferbly a modern and sleek and modern design.
Colors: black, grey, red, white
Information:
Name: Rijwielwerkplaats Vanhoutte
Shop owner: Bart Vanhoutte & Marieke Segers
Website: www.rijwielwerkplaats-vanhoutte.be
Email: info@rijwielwerkplaats-vanhoutte.be
Phone number: +32471902368
Street adres: Kerkweg 46
9940 Bellebeke
Slogan/shop information: Herstellingen van alle merken.
Logo: see files.
Target Market(s)
People who seek a mechanic to fix or upgrade their bikes.
Contact Information for Business Card
Information:
Website: info@rijwielwerkplaats-vanhoutte.be
9940 Bellebeke
Logo: see files.

```html
<!DOCTYPE html>
<html lang="nl">
<head>
<meta charset="utf-8">
<title>Rijwielwerkplaats Vanhoutte – visitekaartje</title>
<link rel="stylesheet" href="https://fonts.googleapis.com/css2?family=Roboto:wght@400;500;700;900&display=swap">
<style>
  :root {
    --bg: #e4e4e4;
    --card: #ffffff;
    --ink: #1c1c1c;
    --muted: #3a3a3a;
    --red: #d9263a;
    --grey: #a7a9ac;
    --panel: #f4f4f4;
  }
  * { box-sizing: border-box; margin: 0; padding: 0; }
  html, body { width: 1200px; height: 852px; overflow: hidden; }
  body {
    background: var(--bg);
    font-family: "Roboto", Arial, sans-serif;
    color: var(--ink);
    display: flex;
    align-items: center;
    justify-content: center;
    gap: 40px;
  }
  .card {
    position: relative;
    width: 540px;
    height: 318px;
    background: var(--card);
    border-radius: 22px;
    overflow: hidden;
    box-shadow: 0 6px 18px rgba(0,0,0,.12);
  }

  /* brand block */
  .brand { display: flex; flex-direction: column; align-items: center; gap: 12px; }
  .brand-mark { width: 42px; height: 42px; border-radius: 50%; background: var(--red); }
  .brand-name {
    font-weight: 900;
    font-size: 25px;
    line-height: 1.08;
    letter-spacing: 1.5px;
    text-transform: uppercase;
    text-align: center;
    color: var(--ink);
  }

  /* front */
  .card--front .brand { position: absolute; left: 0; right: 0; top: 66px; }
  .tagline-rule {
    position: absolute; left: 0; right: 0; top: 236px;
    display: flex; align-items: center; justify-content: center; gap: 14px;
    font-size: 14px; color: var(--muted);
  }
  .tagline-rule::before, .tagline-rule::after {
    content: ""; width: 54px; height: 2px; background: var(--red);
  }
  .front-stripe {
    position: absolute; left: 0; right: 0; bottom: 0; height: 12px;
    background: linear-gradient(90deg, var(--red) 0 62%, var(--grey) 62% 100%);
  }

  /* back */
  .card--back .brand {
    position: absolute; left: 0; top: 0; width: 250px; height: 250px;
    justify-content: center;
  }
  .card--back .brand-name { font-size: 19px; }
  .contact-panel {
    position: absolute; left: 250px; top: 0; right: 0; height: 250px;
    background: var(--panel);
    padding: 54px 22px 0 26px;
  }
  .person-name {
    font-weight: 700; font-size: 21px; letter-spacing: .5px;
    text-transform: uppercase; color: var(--red);
  }
  .person-role { font-size: 13px; color: var(--muted); margin: 2px 0 16px; }
  .contact-list { list-style: none; display: flex; flex-direction: column; gap: 7px; }
  .contact-list li {
    display: flex; align-items: center; gap: 9px;
    font-size: 12.5px; color: var(--ink); white-space: nowrap;
  }
  .contact-list svg { width: 13px; height: 13px; flex: none; fill: var(--red); }
  .back-rule {
    position: absolute; left: 0; right: 0; top: 250px; height: 8px; background: var(--grey);
  }
  .back-band {
    position: absolute; left: 0; right: 0; bottom: 0; height: 60px;
    background: var(--red); color: #fff;
    display: flex; align-items: center; justify-content: center;
    font-size: 15px;
  }
</style>
</head>
<body>

  <section class="card card--front" aria-label="Voorkant">
    <div class="brand">
      <span class="brand-mark"></span>
      <p class="brand-name">Rijwielwerkplaats<br>Vanhoutte</p>
    </div>
    <p class="tagline-rule">Herstellingen van alle merken</p>
    <div class="front-stripe"></div>
  </section>

  <section class="card card--back" aria-label="Achterkant">
    <div class="brand">
      <span class="brand-mark"></span>
      <p class="brand-name">Rijwielwerkplaats<br>Vanhoutte</p>
    </div>

    <div class="contact-panel">
      <h1 class="person-name">Marieke Segers</h1>
      <p class="person-role">Owner</p>
      <ul class="contact-list">
        <li>
          <svg viewBox="0 0 24 24" aria-hidden="true"><path d="M6.6 10.8a15.1 15.1 0 0 0 6.6 6.6l2.2-2.2a1 1 0 0 1 1-.25 11.4 11.4 0 0 0 3.6.57 1 1 0 0 1 1 1V20a1 1 0 0 1-1 1A17 17 0 0 1 3 4a1 1 0 0 1 1-1h3.5a1 1 0 0 1 1 1c0 1.25.2 2.45.57 3.57a1 1 0 0 1-.25 1z"/></svg>
          +32471902368
        </li>
        <li>
          <svg viewBox="0 0 24 24" aria-hidden="true"><path d="M12 2a10 10 0 1 0 0 20 10 10 0 0 0 0-20zm6.9 6h-2.9a15.7 15.7 0 0 0-1.4-3.6A8 8 0 0 1 18.9 8zM12 4c.8 1.2 1.5 2.5 1.9 4h-3.8c.4-1.5 1.1-2.8 1.9-4zM4.3 14a8 8 0 0 1 0-4h3.4a16.5 16.5 0 0 0 0 4zm.8 2h2.9c.3 1.3.8 2.5 1.4 3.6A8 8 0 0 1 5.1 16zM8 8H5.1a8 8 0 0 1 4.3-3.6C8.8 5.5 8.3 6.7 8 8zm4 12c-.8-1.2-1.5-2.5-1.9-4h3.8c-.4 1.5-1.1 2.8-1.9 4zm2.3-6H9.7a14.7 14.7 0 0 1 0-4h4.6a14.7 14.7 0 0 1 0 4zm.3 5.6c.6-1.1 1.1-2.3 1.4-3.6h2.9a8 8 0 0 1-4.3 3.6zm1.7-5.6a16.5 16.5 0 0 0 0-4h3.4a8 8 0 0 1 0 4z"/></svg>
          www.rijwielwerkplaats-vanhoutte.be
        </li>
        <li>
          <svg viewBox="0 0 24 24" aria-hidden="true"><path d="M20 4H4a2 2 0 0 0-2 2v12a2 2 0 0 0 2 2h16a2 2 0 0 0 2-2V6a2 2 0 0 0-2-2zm0 4-8 5-8-5V6l8 5 8-5z"/></svg>
          info@rijwielwerkplaats-vanhoutte.be
        </li>
        <li>
          <svg viewBox="0 0 24 24" aria-hidden="true"><path d="M12 2a7 7 0 0 0-7 7c0 5.25 7 13 7 13s7-7.75 7-13a7 7 0 0 0-7-7zm0 9.5a2.5 2.5 0 1 1 0-5 2.5 2.5 0 0 1 0 5z"/></svg>
          Kerkweg 46 9940 Bellebeke
        </li>
      </ul>
    </div>

    <div class="back-rule"></div>
    <p class="back-band">Herstellingen van alle merken</p>
  </section>

</body>
</html>
```